Dental Practice Billboard Design

We are a newer dental practice in need of a simple but appealing billboard for our growing dental practice to attract new patients. The practice is owned by husband and wife dentists and is family friendly in a small town in Kentucky. We try to be very friendly and caring to our patients. Would prefer a blue background for the billboard and our tooth logo to be prominent. We are partial to the Patua One font used in the image below but please feel free to tweak it as you deem necessary. The shape of the uppercase D and lowercase g are why we like that font, so fonts with a similarly shaped “D” and “g” would work as well. Please include our phone number (555) 847-1390. Please see our website Harlowbrookdentistry.example for more info on the practice if needed. Thank you! Looking forward to seeing your creation.
Updates

The dimensions will be 12ft x 24ft (3.6576m x 7.3152m). Apologies for not including this in the original prompt. Thank you all for your submissions.

Industry/Entity Type

Dental

Font styles to use
Other font styles liked:
• Patua One

Colors
0054AA
0677BA
7BADD7
CADEEF
E8F1F8
0094D4
00A9DD
6FCCEA
C7EBF8
E9F6FB
00AB8E
00BBA5
67D7C9
C6EFE9
E9F9F6
59FF00
82FF00
B8FF75
E3FFCB
F4FFEA

Requirements
Must have
• Phone number, website, Logo, Practice name “Harlow Brook Dentistry”
Should not have
• A tagline or slogan

```html
<!DOCTYPE html>
<html lang="en">
<head>
<meta charset="utf-8">
<title>Harlow Brook Dentistry Billboard</title>
<link rel="stylesheet" href="https://fonts.googleapis.com/css2?family=Patua+One&family=Zilla+Slab:wght@700&display=swap">
<style>
  :root {
    --brand-blue: #31589a;
    --deep-blue: #174a8b;
    --brand-green: #2fa84a;
    --light-green: #6cbf45;
    --paper: #ffffff;
    --backdrop: #e8f1f8;
  }
  html, body {
    margin: 0;
    width: 1200px;
    height: 900px;
    overflow: hidden;
    background: var(--backdrop);
  }
  .billboard {
    position: absolute;
    left: 40px;
    top: 170px;
    width: 1120px;
    height: 560px;
    background: var(--paper);
    overflow: hidden;
    box-shadow: 0 6px 24px rgba(23, 74, 139, 0.18);
  }
  .billboard__art {
    position: absolute;
    inset: 0;
  }
  .copy {
    position: absolute;
    left: 44px;
    top: 34px;
    width: 500px;
    color: var(--brand-blue);
    font-family: "Patua One", "Zilla Slab", serif;
  }
  .brand {
    display: flex;
    align-items: center;
    gap: 12px;
    font-size: 34px;
    line-height: 1;
    color: var(--brand-blue);
  }
  .brand__dot {
    width: 22px;
    height: 22px;
    border-radius: 50%;
    background: var(--brand-green);
  }
  .headline {
    margin: 42px 0 0;
    font-size: 48px;
    line-height: 1.12;
    font-weight: 400;
    white-space: nowrap;
  }
  .services {
    margin-top: 34px;
    font-family: "Zilla Slab", "Patua One", serif;
    font-weight: 700;
  }
  .services__label {
    color: var(--brand-green);
    font-size: 22px;
  }
  .services__list {
    margin: 4px 0 0;
    font-size: 21px;
    line-height: 1.3;
  }
  .phone {
    display: inline-flex;
    align-items: center;
    gap: 14px;
    margin-top: 28px;
    padding: 8px 36px 8px 18px;
    background: var(--brand-green);
    color: var(--paper);
    border-radius: 0 30px 30px 0;
    font-size: 36px;
    line-height: 1.1;
  }
  .website {
    display: flex;
    align-items: center;
    gap: 14px;
    margin-top: 18px;
    font-size: 30px;
    white-space: nowrap;
  }
  .website__arrow {
    flex: none;
  }
</style>
</head>
<body>
  <main class="billboard">
    <svg class="billboard__art" width="1120" height="560" viewBox="0 0 1120 560">
      <defs>
        <linearGradient id="photo-tone" x1="0" y1="0" x2="1" y2="1">
          <stop offset="0" stop-color="#f4f6f8"/>
          <stop offset="0.55" stop-color="#dfe6ee"/>
          <stop offset="1" stop-color="#b9c6d6"/>
        </linearGradient>
      </defs>
      <path class="blue-band" d="M560,0 C560,240 650,450 770,560 L1120,560 L1120,0 Z" fill="#174a8b"/>
      <path class="green-edge" d="M580,300 C615,420 670,500 740,560 L710,560 C650,500 600,420 580,300 Z" fill="#2fa84a"/>
      <path class="green-arc" d="M655,0 C635,230 700,440 810,560 L1000,560 L1000,0 Z" fill="#6cbf45"/>
      <path class="photo-area" role="img" aria-label="Photo of the two smiling dentists in white coats"
            d="M695,0 C665,220 720,430 830,560 L1120,560 L1120,0 Z" fill="url(#photo-tone)"/>
    </svg>

    <section class="copy">
      <div class="brand"><span class="brand__dot"></span>Harlow Brook Dentistry</div>
      <h1 class="headline">A Home for Healthy,<br>Happy Smiles</h1>
      <div class="services">
        <div class="services__label">Services:</div>
        <p class="services__list">Crowns Root Canals, Extractions, Implants,<br>Bridges, Clear Aligners, Veneers, Whitening,<br>Fillings, Cleanings, Dentures</p>
      </div>
      <div class="phone">
        <svg width="30" height="30" viewBox="0 0 24 24" aria-hidden="true">
          <path d="M6.6 10.8a15 15 0 0 0 6.6 6.6l2.2-2.2a1 1 0 0 1 1-.25 11.4 11.4 0 0 0 3.6.57 1 1 0 0 1 1 1V20a1 1 0 0 1-1 1A17 17 0 0 1 3 4a1 1 0 0 1 1-1h3.5a1 1 0 0 1 1 1c0 1.25.2 2.45.57 3.57a1 1 0 0 1-.25 1Z" fill="#ffffff"/>
        </svg>
        (555) 847-1390
      </div>
      <div class="website">
        <svg class="website__arrow" width="28" height="28" viewBox="0 0 24 24" aria-hidden="true">
          <path d="M3 3 L21 10 L13.5 12.5 L19 18 L17 20 L11.5 14.5 L9 21 Z" fill="#2fa84a"/>
        </svg>
        www.harlowbrookdentistry.example
      </div>
    </section>
  </main>
</body>
</html>
```